Business Card Design for Brindle Consulting

I need business cards for a new company I have started called Brindle Consulting. Brindle Consulting is a new business based out of Columbus Ohio. I will be operating in Ohio as well as nationwide. Brindle Consulting is a professional organization designed to fit your organization's specific needs. We are dedicated to the success of organizations. We handle human resource management, leadership coaching and development, executive training, team building, personality inventories and searches, performance evaluations, temp. services, custom solutions and more. Brindle consulting services a variety of industries such as government agencies, educational systems, board of directors, construction services and more, please visit our website for a full list of services (the website will be important).

I leave the design to you. I am a 45 year old male. I was in the education field for 21 years and 11 years as a superintendent. I like the colors red and black. Don't know what works, I will leave that to you as well. I would like to have it be catchy yet masculine. I have been associated with many organizations over the years both public and private, and will be reaching out to the public and private sector.

I do need a logo...so I leave that to you as well. Company name is Brindle Consulting.

Industry/Entity Type

Construction

Contact Information for Business Card

Gordon T. Brindle, President
Brindle Consulting
48 W.Fifth St. Suite 305
Arcade at Halvern Court
Columbus, Ohio 43287

Phone : 330-555-4178
email : gbrindle@brindleadvise.example
web : www.brindleadvise.example
twitter : @brindleadvise
facebook : Brindle Consulting

```html
<!DOCTYPE html>
<html lang="en">
<head>
<meta charset="utf-8">
<title>Brindle Consulting – Business Card</title>
<link rel="stylesheet" href="https://fonts.googleapis.com/css2?family=Arimo:wght@400;700&family=Michroma&display=swap">
<style>
  :root {
    --stage: #1c1c1c;
    --brand-blue: #00b0ef;
    --card-light: #ffffff;
    --card-shade: #d9d9d9;
    --text-dark: #2b2b2b;
    --text-mid: #444444;
    --back-text: #1f4f63;
  }
  * { margin: 0; padding: 0; box-sizing: border-box; }
  html, body {
    width: 1200px;
    height: 908px;
    overflow: hidden;
    background: var(--stage);
  }
  .stage {
    position: relative;
    width: 1200px;
    height: 908px;
    display: flex;
    align-items: center;
    justify-content: center;
    gap: 40px;
  }
  .card {
    position: relative;
    width: 520px;
    height: 300px;
    border-radius: 22px;
    overflow: hidden;
  }
  /* Back side */
  .card-back {
    background: var(--brand-blue);
    display: flex;
    align-items: center;
    justify-content: center;
  }
  .card-back .back-name {
    font-family: "Michroma", sans-serif;
    font-variant: small-caps;
    font-size: 11px;
    letter-spacing: 2px;
    color: var(--back-text);
  }
  /* Front side */
  .card-front {
    background: radial-gradient(ellipse at 62% 40%, var(--card-light) 0%, #f3f3f3 35%, var(--card-shade) 100%);
  }
  .company-name {
    position: absolute;
    top: 38px;
    right: 34px;
    font-family: "Michroma", sans-serif;
    font-variant: small-caps;
    font-size: 17px;
    letter-spacing: 2px;
    color: var(--brand-blue);
  }
  .identity {
    position: absolute;
    top: 92px;
    left: 22px;
    padding-left: 12px;
    border-left: 4px solid var(--brand-blue);
    font-family: "Arimo", sans-serif;
  }
  .person-name {
    font-size: 17px;
    font-weight: 700;
    color: var(--brand-blue);
    line-height: 20px;
  }
  .person-title {
    font-size: 12px;
    color: var(--text-mid);
    line-height: 16px;
  }
  .contact {
    position: absolute;
    top: 150px;
    left: 38px;
    font-family: "Arimo", sans-serif;
    font-size: 12.5px;
    line-height: 15px;
    color: var(--text-dark);
  }
  .contact .phone {
    font-weight: 700;
    font-size: 13.5px;
  }
  .contact .address {
    margin-top: 16px;
  }
  .brand-band {
    position: absolute;
    left: 0;
    right: 0;
    bottom: 0;
    height: 44px;
    background: var(--brand-blue);
  }
</style>
</head>
<body>
  <main class="stage">
    <section class="card card-back" aria-label="Card back">
      <p class="back-name">Brindle Consulting</p>
    </section>

    <section class="card card-front" aria-label="Card front">
      <p class="company-name">Brindle Consulting</p>
      <div class="identity">
        <p class="person-name">JOHN CARVER</p>
        <p class="person-title">GENERAL MANAGER</p>
      </div>
      <div class="contact">
        <p class="phone">(012) 555 0189</p>
        <p class="email">info@yourmail.example</p>
        <p class="web">www.urwebsite.example</p>
        <p class="address">1040 Lakeview AVE,<br>NY Ridgeford, USA</p>
      </div>
      <div class="brand-band"></div>
    </section>
  </main>
</body>
</html>
```